Stationary Design for Quince consultant and support company

We need new stationary designed for a London based support company that provide on-site and remote support services for Quince products. Our clients are both consumers and businesses.

We would like a letterhead, compliment slip, business card and possibly an e-mail signature designed.

Business card designs can be either 1 side or 2, depending on designs we receive we may choose a preference for 1 or 2 sides later on in the design stage.

Designs needs to be at least 300dpi and should be done using CMYK colours.

We want the design to be bold, easy to read, clean and professional.

We have attached our company logo in 2 colour variations (if you need any other source files then please ask).

Our logo colours are as follows:

Blue (85, 50, 0, 0) and Green (50, 0, 100, 0)

We use two different suppliers for out stationary so here are the size dimensions for both. Unfortunately they are ever so slightly different size wise so hopefully we can get something that accommodates both, we can provide dimensions if required for final versions.

Some fonts that have been used before with our company are Probert (for tagline on our company logo) and previously had Nauman used, however we are very much open to seeing what the designers come up with and the fonts mentioned are not a requirement.
Updates

Company details for designs (however the template should be editable for multiple staff) Lumora Ltd. Registered Office: 62-70 Harrowfield Lane London N7 3QD 020 7591 3384 www.lumora-it.example info@lumora-it.example Company is Registered in England and Wales Company No. 07342519 Directors details (if you want to make the template using his details), rest of the details are as above Dan Frost Director dan@lumora-it.example

Hi all, Thank you for your submissions so far. Could we please ask that you don't use the logo with the tagline from our website for the stationary designs and only the logos provided in the design brief. For the business cards we are looking at normal rectangular business cards to be used and we can provide a template guide for size if needed, please just ask. Regards Lumora Team

Target Market(s)

Our target market are consumers (of all ages) and small/medium businesses.

Industry/Entity Type

Business

Font styles to use
Serif
Sans Serif

Requirements
Must have
• At least business card, letterhead and compliment slip submitted (we need all 3 designed this time round)
Should not have
• Business cards should not have the writing "registered office" (letterheads and compliment slips can along the bottom edge)

```html
<!DOCTYPE html>
<html lang="en">
<head>
<meta charset="utf-8">
<title>Lumora Ltd. Stationery</title>
<link href="https://fonts.googleapis.com/css2?family=Titillium+Web:wght@400;600;700&display=swap" rel="stylesheet">
<style>
  :root {
    --brand-blue: #1f78c1;
    --brand-green: #8dc63f;
    --ink: #1d1d1b;
    --body-text: #555a5f;
    --muted: #8a8f94;
    --paper: #ffffff;
    --backdrop: #ebebeb;
    --shadow: 0 6px 18px rgba(0,0,0,0.12);
  }
  * { box-sizing: border-box; margin: 0; padding: 0; }
  html, body { width: 1200px; height: 1000px; overflow: hidden; }
  body {
    background: var(--backdrop);
    font-family: "Titillium Web", Arial, sans-serif;
    color: var(--body-text);
    position: relative;
  }
  .sheet { position: absolute; background: var(--paper); box-shadow: var(--shadow); }
  .wordmark {
    font-family: "Titillium Web", Arial, sans-serif;
    font-weight: 700;
    color: var(--ink);
    letter-spacing: 0.06em;
    text-transform: uppercase;
    display: flex; align-items: center; gap: 6px;
  }
  .wordmark-dot { display: inline-block; background: var(--brand-green); }

  /* Letterhead */
  .letterhead { left: 50px; top: 104px; width: 560px; height: 792px; }
  .letterhead .wordmark { position: absolute; left: 48px; top: 44px; font-size: 30px; }
  .letterhead .wordmark-dot { width: 12px; height: 12px; }
  .letter-body { position: absolute; left: 140px; top: 130px; width: 370px; font-size: 10.5px; line-height: 1.55; }
  .letter-body .salutation { font-style: italic; margin-bottom: 14px; font-size: 11.5px; }
  .letter-body p { margin-bottom: 12px; }
  .letter-body .closing { text-align: right; font-style: italic; margin-top: 26px; font-size: 11.5px; }
  .signature-area {
    position: absolute; left: 330px; top: 610px; width: 160px; height: 40px;
    background: linear-gradient(90deg, rgba(29,29,27,0.08), rgba(29,29,27,0.02));
    border-radius: 4px;
  }
  .brand-panel {
    position: absolute; left: 48px; top: 520px; width: 120px; height: 120px;
    background: var(--brand-blue); opacity: 0.75;
  }
  .sheet-footer {
    position: absolute; left: 48px; right: 48px; bottom: 40px;
    display: flex; justify-content: space-between;
    font-size: 8.5px; line-height: 1.5; color: var(--muted);
    border-top: 1px solid var(--brand-blue); padding-top: 8px;
  }
  .sheet-footer strong { color: var(--brand-blue); font-weight: 600; }

  /* Business cards */
  .card { width: 260px; height: 168px; top: 104px; }
  .card-front { left: 650px; display: flex; align-items: center; justify-content: center; }
  .card-front .wordmark { font-size: 28px; }
  .card-front .wordmark-dot { width: 11px; height: 11px; }
  .card-back { left: 930px; }
  .card-back .wordmark { position: absolute; right: 18px; top: 18px; font-size: 16px; }
  .card-back .wordmark-dot { width: 7px; height: 7px; }
  .card-person { position: absolute; left: 18px; top: 62px; }
  .card-name { color: var(--brand-blue); font-size: 15px; font-weight: 600; line-height: 1.1; }
  .card-role { color: var(--brand-green); font-size: 11px; }
  .card-rule { position: absolute; left: 18px; right: 18px; top: 108px; border-top: 1px solid var(--brand-blue); }
  .card-contacts {
    position: absolute; left: 18px; right: 18px; top: 116px;
    display: flex; justify-content: space-between; font-size: 8px; line-height: 1.5; color: var(--muted);
  }

  /* Compliment slip */
  .comp-slip { left: 650px; top: 330px; width: 530px; height: 250px; }
  .comp-slip .wordmark { position: absolute; right: 32px; top: 30px; font-size: 26px; }
  .comp-slip .wordmark-dot { width: 10px; height: 10px; }
  .comp-title { position: absolute; left: 32px; top: 150px; font-size: 22px; font-weight: 400; }
  .comp-title .lead { color: var(--brand-blue); }
  .comp-title .accent { color: var(--brand-green); }
  .comp-slip .sheet-footer { left: 32px; right: 32px; bottom: 22px; }
</style>
</head>
<body>

<section class="sheet letterhead" aria-label="Letterhead">
  <div class="wordmark">Lumora<span class="wordmark-dot"></span></div>
  <div class="letter-body">
    <p class="salutation">Dear Client,</p>
    <p>Thank you for choosing us to look after your devices. Our engineers provide on-site visits and remote sessions across London, helping homes and small offices keep every system running smoothly and securely through the year.</p>
    <p>Each plan includes setup, updates, backup checks and quick fixes, with a named contact who knows your equipment and answers promptly.</p>
    <p>We review your network, storage and accounts at regular intervals and share a clear summary of what we found, what we changed and what we recommend next.</p>
    <p>Please get in touch whenever you need help. We look forward to working with you.</p>
    <p class="closing">Best regards,</p>
  </div>
  <div class="brand-panel"></div>
  <div class="signature-area" role="img" aria-label="Handwritten signature of Ellis Warden"></div>
  <footer class="sheet-footer">
    <div><strong>Lumora Ltd.</strong><br>Registered Office: 62-70 Harrowfield Lane<br>London N7 3QD</div>
    <div>www.lumora-it.example<br>info@lumora-it.example</div>
    <div>020 7591 3384<br>Company No. 07342519</div>
  </footer>
</section>

<section class="sheet card card-front" aria-label="Business card front">
  <div class="wordmark">Lumora<span class="wordmark-dot"></span></div>
</section>

<section class="sheet card card-back" aria-label="Business card back">
  <div class="wordmark">Lumora<span class="wordmark-dot"></span></div>
  <div class="card-person">
    <div class="card-name">Dan Frost</div>
    <div class="card-role">Director</div>
  </div>
  <div class="card-rule"></div>
  <div class="card-contacts">
    <div>62-70 Harrowfield Lane<br>London N7 3QD</div>
    <div>dan@lumora-it.example<br>020 7591 3384</div>
  </div>
</section>

<section class="sheet comp-slip" aria-label="Compliment slip">
  <div class="wordmark">Lumora<span class="wordmark-dot"></span></div>
  <h2 class="comp-title"><span class="lead">With</span> <span class="accent">Compliments.</span></h2>
  <footer class="sheet-footer">
    <div><strong>Lumora Ltd.</strong><br>62-70 Harrowfield Lane, London N7 3QD</div>
    <div>www.lumora-it.example<br>info@lumora-it.example</div>
    <div>020 7591 3384</div>
  </footer>
</section>

</body>
</html>
```